Powerpoint, Graphics for Sermon Series

I am starting a sermon series on the short letters if Scripture that are between Hebrews and Revelation. The sermon series will be called "Walking Unmarked Trails: Lasting Lessons from Quiet Hills."

Think about finding a packet of letters in an Attic. There is only the dialogue of the writer. We don't know exactly what the receivers were going through or even what their response to the letters were/are!

Target Market(s)

Local Church

Industry/Entity Type

Christian

Font styles to use
Serif
Sans Serif

Colors

Designer to choose colors to be used in the design.

Requirements
Must have
• Powerpoint Slide with Title -
• Background Slide -
• It would be great to have both JPG, PNG, and Photoshop/Indesign that can be used for powerpoint, both in 4x3 ration and wide... Need Title Slide with typography and background slide for text to go over the top of.
• Stick with the theme -- Walking Unmarked Trails
• I am including our church logo, but don't feel like you need to use it in anyway.
Nice to have
• Social Media Slides - Square Slide, Facebook Header
• Greyscale Version?

```html
<!DOCTYPE html>
<html lang="en">
<head>
<meta charset="utf-8">
<title>Walking Unmarked Trails – Content Slide</title>
<link href="https://fonts.googleapis.com/css2?family=Roboto+Slab:wght@700&family=Lato:wght@400;700&display=swap" rel="stylesheet">
<style>
  :root {
    --title-brown: #5b3a26;
    --accent-orange: #f0a012;
    --subhead-orange: #c47d16;
    --body-text: #262320;
    --page-white: #ffffff;
    --haze-light: #fbf7f3;
    --haze-warm: #efe3d8;
    --amber-light: #d98a2c;
    --amber-deep: #a24e12;
    --amber-dark: #6e2f0a;
  }
  * { margin: 0; padding: 0; box-sizing: border-box; }
  html, body { width: 1200px; height: 900px; overflow: hidden; background: var(--page-white); }
  .slide {
    position: relative;
    width: 1200px;
    height: 900px;
    overflow: hidden;
    background: var(--page-white);
  }
  .slide__backdrop {
    position: absolute;
    inset: 0;
    background: linear-gradient(180deg, var(--haze-light) 0%, var(--haze-warm) 45%, #f6eee7 70%, var(--haze-light) 100%);
  }
  .slide__frame { position: absolute; inset: 0; }
  .slide__heading {
    position: absolute;
    left: 0;
    top: 24px;
    padding: 0 28px 6px 48px;
    border-bottom: 3px solid var(--accent-orange);
  }
  .slide__title {
    font-family: "Roboto Slab", "Rockwell", Georgia, serif;
    font-weight: 700;
    font-size: 52px;
    letter-spacing: 0.3px;
    color: var(--title-brown);
    line-height: 1.3;
    white-space: nowrap;
  }
  .column {
    position: absolute;
    top: 160px;
    width: 468px;
    font-family: "Lato", Arial, sans-serif;
  }
  .column--left { left: 50px; }
  .column--right { left: 575px; }
  .column__heading {
    font-weight: 700;
    font-size: 33px;
    color: var(--subhead-orange);
    line-height: 1.25;
    margin-bottom: 4px;
  }
  .column__body {
    font-weight: 400;
    font-size: 22px;
    line-height: 37.6px;
    color: var(--body-text);
  }
  .church-name {
    position: absolute;
    left: 20px;
    top: 832px;
    display: flex;
    align-items: center;
    gap: 10px;
    font-family: "Lato", Arial, sans-serif;
    font-weight: 700;
    font-size: 24px;
    color: var(--title-brown);
  }
  .church-name__mark {
    width: 16px;
    height: 16px;
    background: var(--title-brown);
  }
</style>
</head>
<body>
  <main class="slide">
    <div class="slide__backdrop" role="img" aria-label="Faint sunset sky over a quiet hillside trail"></div>

    <svg class="slide__frame" width="1200" height="900" viewBox="0 0 1200 900">
      <defs>
        <linearGradient id="amberPhoto" x1="0" y1="0" x2="0.4" y2="1">
          <stop offset="0%" stop-color="#d98a2c"/>
          <stop offset="50%" stop-color="#a24e12"/>
          <stop offset="100%" stop-color="#6e2f0a"/>
        </linearGradient>
      </defs>
      <path role="img" aria-label="Warm amber photo of an open Bible with a bundle of old letters"
            d="M955,0 C1095,150 1150,420 1088,650 C1045,770 975,850 900,900 L1200,900 L1200,0 Z"
            fill="url(#amberPhoto)"/>
      <path d="M985,0 L1200,0 L1200,40 C1160,160 1140,330 1112,640 C1150,420 1100,170 985,0 Z"
            fill="#f0a012"/>
      <path d="M1030,0 L1048,0 C1150,140 1178,330 1112,640 C1160,360 1120,150 1030,0 Z"
            fill="#ffffff"/>
    </svg>

    <header class="slide__heading">
      <h1 class="slide__title">Walking Unmarked Trails</h1>
    </header>

    <section class="column column--left">
      <h2 class="column__heading">Subtext title here</h2>
      <p class="column__body">Lorem Ipsum is simply dummy text of the print&shy;ing and typesetting industry. Lorem Ipsum has been the industry's standard dummy text ever since the 1500s, when an unknown printer took a galley of type and scrambled it to make a type specimen book. It has survived not only five centuries, but also the leap into electronic typesetting, remaining essentially unchanged. It was popularised in the 1960s with the release of Letraset sheets containing Lorem Ipsum passages, and more recently with desk&shy;top publishing software like Aldus PageMaker including versions of Lorem Ipsum. It has sur&shy;vived not only five centuries</p>
    </section>

    <section class="column column--right">
      <h2 class="column__heading">Subtext title here</h2>
      <p class="column__body">Lorem Ipsum is simply dummy text of the print&shy;ing and typesetting industry. Lorem Ipsum has been the industry's standard dummy text ever since the 1500s, when an unknown printer took a galley of type and scrambled it to make a type specimen book. It has survived not only five centuries, but also the leap into electronic typesetting, remaining essentially unchanged. It was popularised in the 1960s with the release of Letraset sheets containing Lorem Ipsum passages, and more recently with desk&shy;top publishing software like Aldus PageMaker including versions of Lorem Ipsum. It has sur&shy;vived not only five centuries</p>
    </section>

    <div class="church-name">
      <span class="church-name__mark"></span>
      <span class="church-name__text">Cedar Hollow Church</span>
    </div>
  </main>
</body>
</html>
```